Business Card Design

We like to use greens as you will see in our logo (but not TOO much green). We are a Dental Clinic in a somewhat eccentric community. We do not like the dated sharp designs which we see many dentists use. We're looking for something bright and fresh while still maintaining the integrity of the profession. Elegance is not necessarily what we are going for... we need for the design to be "mature" but also up-lifting.

See our logo.
Updates

Project Deadline Extended
Reason: We have 5 designs which we like. But we'd like to see a few more before committing to a design.

Project Deadline Extended
Reason: We are awaiting revisions to this project. We are still welcoming designs while we wait to see if designers are able to provide to us the revisions we require in order to proceed with a selection.

Target Market(s)

Younger families - ages late 20's to early 40's

Industry/Entity Type

Business

Contact Information for Business Card

Corwel T. Banfry DDS 2730 W. Halvert Rd. Ste. 7 Royal Oak, MI 48391 (248)555-0174 FX (248)555-0189 info@BrightwellDentalCareMi.com BrigthwellDentalCareMi.com on the back of the card we need an appointment reminder (For____ Date___ Time____) with "If you are unable to keep your appointment, kindly give 48 hours notice" at the bottom. No use of teeth in the design. DOUBLE SIDED DESIGN

Requirements
Should not have
• The use of pictures of teeth

```html
<!DOCTYPE html>
<html lang="en">
<head>
<meta charset="utf-8">
<title>Brightwell Dental Care – Business Card</title>
<link rel="stylesheet" href="https://fonts.googleapis.com/css2?family=Source+Sans+3:ital,wght@0,400;0,600;0,700;1,400;1,600&family=Cinzel:wght@500&display=swap">
<style>
  :root{
    --green-deep:#1f6b34;
    --green-mid:#2f8a3a;
    --green-bright:#3fa737;
    --green-lime:#8cc63f;
    --ink:#333333;
    --paper:#ffffff;
    --backdrop:#e9ece6;
    --rule:#8a8a8a;
  }
  *{box-sizing:border-box;margin:0;padding:0}
  html,body{width:1200px;height:1178px;overflow:hidden}
  body{background:var(--backdrop);position:relative;font-family:"Source Sans 3",Arial,sans-serif;color:var(--ink)}

  .card{position:absolute;background:var(--paper);border-radius:30px;overflow:hidden;box-shadow:0 2px 6px rgba(0,0,0,.18)}
  .card--front{left:237px;top:45px;width:918px;height:525px}
  .card--back{left:27px;top:605px;width:918px;height:520px;border:2px solid #555}

  .wordmark{position:absolute;text-align:center;color:var(--green-deep);font-family:"Source Sans 3",Arial,sans-serif;font-weight:600;line-height:1}
  .wordmark__name{display:block}
  .wordmark__sub{display:block;letter-spacing:.04em}
  .card--front .wordmark{left:0;right:0;top:95px}
  .card--front .wordmark__name{font-size:84px}
  .card--front .wordmark__sub{font-size:40px;margin-top:10px}
  .card--back .wordmark{left:630px;width:270px;top:55px}
  .card--back .wordmark__name{font-size:50px}
  .card--back .wordmark__sub{font-size:24px;margin-top:6px}

  .dentist{position:absolute;left:0;right:0;top:283px;text-align:center;color:var(--green-deep);font-weight:700;font-size:29px}
  .dentist small{font-weight:400;font-size:22px}

  .front-band{position:absolute;left:0;top:0;width:918px;height:525px}

  .contact{position:absolute;left:0;right:0;color:#fff;font-size:21px;display:flex;justify-content:center;align-items:center;gap:10px}
  .contact svg{width:18px;height:18px;fill:#fff;flex:none}
  .contact--phones{top:384px}
  .contact--web{top:424px}
  .contact--address{top:476px}
  .contact__item{display:inline-flex;align-items:center;gap:5px}

  .appt-title{position:absolute;left:73px;top:100px;font-family:"Cinzel",Georgia,serif;font-weight:500;font-size:33px;color:var(--green-deep);letter-spacing:.02em}

  .field{position:absolute;font-size:24px;display:flex;align-items:baseline;color:var(--ink)}
  .field__dots{border-bottom:2px dotted var(--rule);height:1px;display:inline-block;margin:0 8px}
  .field--name{left:80px;top:178px;width:780px}
  .field--name .field__dots{flex:1;margin-left:20px}
  .field--date{left:80px;top:246px;width:820px}
  .field--date .field__dots--date{width:225px;margin-left:28px}
  .field--date .field__dots--time{width:240px}
  .field--next{left:80px;top:309px;align-items:center}
  .next-box{width:166px;height:36px;border:2px solid #555;border-radius:7px;margin-left:12px}
  .next-box:first-of-type{margin-left:56px}

  .days{position:absolute;left:0;top:363px;width:918px;height:75px;display:flex}
  .days__main{width:733px;background:var(--green-deep);display:flex;align-items:center;padding-left:80px;gap:0}
  .days__sat{flex:1;background:var(--green-bright);border-left:3px solid #fff;display:flex;align-items:center;padding-left:28px}
  .day{display:flex;align-items:center;color:#fff;font-weight:700;font-size:25px;margin-right:16px}
  .day__box{width:54px;height:33px;background:#fff;border-radius:5px;margin-left:14px}

  .notice{position:absolute;left:0;right:0;top:462px;text-align:center;font-style:italic;font-weight:600;font-size:24px;color:var(--ink)}
</style>
</head>
<body>

<section class="card card--front" aria-label="Business card front">
  <svg class="front-band" viewBox="0 0 918 525" aria-hidden="true">
    <path d="M0 302 Q460 422 918 262 L918 525 L0 525 Z" fill="var(--green-deep)"/>
    <path d="M0 284 Q460 404 918 246" fill="none" stroke="var(--green-lime)" stroke-width="5"/>
  </svg>

  <div class="wordmark">
    <span class="wordmark__name">Brightwell</span>
    <span class="wordmark__sub">DENTAL CARE</span>
  </div>

  <p class="dentist">Corwel T. Banfry, <small>DDS</small></p>

  <p class="contact contact--phones">
    <span class="contact__item">
      <svg viewBox="0 0 24 24"><path d="M6.6 10.8a15 15 0 0 0 6.6 6.6l2.2-2.2c.3-.3.7-.4 1-.2 1.1.4 2.3.6 3.6.6.6 0 1 .4 1 1V20c0 .6-.4 1-1 1A17 17 0 0 1 3 4c0-.6.4-1 1-1h3.5c.6 0 1 .4 1 1 0 1.3.2 2.5.6 3.6.1.3 0 .7-.2 1z"/></svg>
      (248)555-0174
    </span>
    <span class="contact__item">
      <svg viewBox="0 0 24 24"><path d="M6 3h10v5H6zM3 9h18v9h-3v3H6v-3H3zm5 7v3h8v-3z"/></svg>
      (248)555-0189
    </span>
  </p>
  <p class="contact contact--web">
    <span class="contact__item">
      <svg viewBox="0 0 24 24"><path d="M2 6h20v12H2zm2 2v.5l8 5 8-5V8l-8 5z"/></svg>
      info@BrightwellDentalCareMi.com
    </span>
    <span class="contact__item">
      <svg viewBox="0 0 24 24"><path d="M12 2a10 10 0 1 0 0 20 10 10 0 0 0 0-20zm6.9 9h-3a15 15 0 0 0-1.3-6A8 8 0 0 1 18.9 11zM12 4.1c.9 1.3 1.7 3.9 1.9 6.9h-3.8c.2-3 1-5.6 1.9-6.9zM9.4 5a15 15 0 0 0-1.3 6h-3A8 8 0 0 1 9.4 5zM5.1 13h3a15 15 0 0 0 1.3 6A8 8 0 0 1 5.1 13zm6.9 6.9c-.9-1.3-1.7-3.9-1.9-6.9h3.8c-.2 3-1 5.6-1.9 6.9zm2.6-.9a15 15 0 0 0 1.3-6h3a8 8 0 0 1-4.3 6z"/></svg>
      BrigthwellDentalCareMi.com
    </span>
  </p>
  <p class="contact contact--address">2730 W. Halvert Rd. Ste. 7 Royal Oak, MI 48391</p>
</section>

<section class="card card--back" aria-label="Appointment card back">
  <h1 class="appt-title">YOUR APPOINTMENT</h1>

  <div class="wordmark">
    <span class="wordmark__name">Brightwell</span>
    <span class="wordmark__sub">DENTAL CARE</span>
  </div>

  <p class="field field--name">Name :<span class="field__dots"></span></p>
  <p class="field field--date">Date :<span class="field__dots field__dots--date"></span>Time :<span class="field__dots field__dots--time"></span>am / pm</p>
  <div class="field field--next">Next Appointment<span class="next-box"></span><span class="next-box"></span><span class="next-box"></span></div>

  <div class="days">
    <div class="days__main">
      <span class="day">MON<span class="day__box"></span></span>
      <span class="day">TUE<span class="day__box"></span></span>
      <span class="day">WED<span class="day__box"></span></span>
      <span class="day">THU<span class="day__box"></span></span>
      <span class="day">FRI<span class="day__box"></span></span>
    </div>
    <div class="days__sat">
      <span class="day">SAT<span class="day__box"></span></span>
    </div>
  </div>

  <p class="notice">If you are unable to keep your appointment, kindly give 48 hours notice</p>
</section>

</body>
</html>
```